Corvane Spectrix Holdings - Business Cards

I would like a design developed using the logo (number 60387519) previously developed and attached. The information needs to include everything shown on the attached email title block, arranged to suit a business format. I would like a white background, with no other graphics added.
I need an editable version (e.g. MSWord) so I can change the name shown on the business card for others.

Target Market(s)

Mining & Heavy Manufacturing industries

Industry/Entity Type

Mining

Contact Information for Business Card

Refer to attached email title block in MSWord format for the details to be included.

Colors

Designer to choose colors to be used in the design.

Requirements
Must have
• White background, and fonts and text colour to match the unique font in the logo.
Nice to have
• the website address to be shown along the bottom of the card, as it is quite long.
Should not have
• Dark background, or unnecessary graphics

```html
<!DOCTYPE html>
<html lang="en">
<head>
<meta charset="utf-8">
<title>Corvane Spectrix Holdings – Business Card</title>
<link rel="stylesheet" href="https://fonts.googleapis.com/css2?family=Questrial&family=Varela+Round&display=swap">
<style>
  :root {
    --stage: #e9ebee;
    --card: #ffffff;
    --card-shade: #eef0f3;
    --brand-blue: #1e78d0;
    --band-blue: #2f7ad3;
    --ink: #1b1b1b;
    --light-blue: #3a8fe0;
  }
  * { margin: 0; padding: 0; box-sizing: border-box; }
  html, body {
    width: 1200px; height: 838px; overflow: hidden;
    background: var(--stage);
  }
  .stage {
    position: relative; width: 1200px; height: 838px;
    display: flex; align-items: center; justify-content: center;
  }
  .card {
    position: relative; width: 1000px; height: 610px;
    background: linear-gradient(160deg, var(--card) 45%, var(--card-shade) 100%);
    box-shadow: 0 10px 30px rgba(0,0,0,0.18);
    overflow: hidden;
    font-family: "Questrial", "Century Gothic", sans-serif;
    color: var(--ink);
  }
  .brand {
    position: absolute; left: 64px; top: 52px;
    display: flex; align-items: center; gap: 18px;
  }
  .brand-dot {
    width: 58px; height: 58px; border-radius: 50%;
    background: var(--brand-blue);
  }
  .brand-name {
    font-family: "Questrial", "Century Gothic", sans-serif;
    color: var(--brand-blue);
    font-size: 34px; line-height: 1.05; letter-spacing: 3px;
    text-transform: uppercase;
  }
  .person {
    position: absolute; left: 64px; top: 200px;
  }
  .person-name {
    font-family: "Varela Round", "Nunito", sans-serif;
    color: var(--brand-blue);
    font-size: 40px; font-weight: 700; line-height: 1.1;
    -webkit-text-stroke: 0.6px var(--brand-blue);
  }
  .person-role {
    color: var(--light-blue);
    font-size: 32px; line-height: 1.15;
  }
  .contact {
    position: absolute; left: 64px; top: 300px; right: 64px;
    font-size: 27px; line-height: 1.25;
  }
  .contact-email {
    display: block;
    border-bottom: 2px solid var(--brand-blue);
    padding-bottom: 2px; margin-bottom: 4px;
  }
  .address {
    position: absolute; right: 64px; bottom: 118px;
    text-align: right; font-size: 27px; line-height: 1.2;
    text-transform: uppercase;
  }
  .address .town { text-transform: none; }
  .web-band {
    position: absolute; left: 0; right: 0; bottom: 0; height: 86px;
    background: var(--band-blue);
    display: flex; align-items: center; justify-content: flex-end;
    padding-right: 64px;
  }
  .web-address {
    color: #ffffff; font-size: 28px; letter-spacing: 0.5px;
  }
</style>
</head>
<body>
  <main class="stage">
    <article class="card">
      <header class="brand">
        <span class="brand-dot" aria-hidden="true"></span>
        <div class="brand-name">Corvane<br>Spectrix<br>Holdings</div>
      </header>

      <section class="person">
        <h1 class="person-name">Teodoro (Teo) Varga</h1>
        <p class="person-role">Director</p>
      </section>

      <section class="contact">
        <span class="contact-email">teodoro.varga@corvanespectrixholdings.com.au</span>
        <span class="contact-phone">+61 432 807 915</span><br>
        <span class="contact-messenger">mtk.teodoro.varga</span>
      </section>

      <address class="address">
        PO BOX 57, <span class="town">Marlow</span><br>
        NSW 2406, AUSTRALIA<br>
        ABN 48 305 172 936
      </address>

      <footer class="web-band">
        <span class="web-address">www.corvanespectrixholdings.com.au</span>
      </footer>
    </article>
  </main>
</body>
</html>
```